NEW Modern Sleek Business Card for VR Language Startup

Our startup is using VR to lead the next wave of world language education. We need a two-sided business card that introduces the larger organization (Brightloom Language Inc) and our contact info on one side and shows the product, Glimwoorld, on the other side.

Side 1 (contact info)= Brightloom Logo and Contact info (name, title, phone, email)

Side 2 (product)= Glimworld logo, text, and website
Text= Culturally Immersive Language Learning Games
Website= www.glimworld-play.com

Target Market(s)

Education, Technology

Contact Information for Business Card

Contact info will be updated upon approval of the design. For now, put this as a placeholder.

Perry Dunmore
Founder & CEO
pdunmore@quillpost-mail.net
(555)-014-2286

Font styles to use
Other font styles liked:
• Gibson and Century Gothic are the brand fonts

Requirements
Nice to have
• I would love to see cohesion between the design and colors of the two logos. I have attached a few business card designs that I like, so you can get a feel for my preferred style.

```html
<!DOCTYPE html>
<html lang="en">
<head>
<meta charset="utf-8">
<title>Brightloom Language – Business Card</title>
<link rel="stylesheet" href="https://fonts.googleapis.com/css2?family=Montserrat:wght@400;500;600;700&family=Questrial&display=swap">
<style>
  :root {
    --page-bg: #e9e9ec;
    --card-bg: #ffffff;
    --ink: #2a2a2c;
    --ink-soft: #4a4a4e;
    --violet: #5b3df5;
    --accent-red: #ef2b3a;
    --warm-1: #f4a93a;
    --warm-2: #f7343f;
    --warm-3: #7c5ce8;
    --cool-1: #22d8ec;
    --cool-2: #6a55f6;
  }
  * { box-sizing: border-box; margin: 0; padding: 0; }
  html, body {
    width: 1200px; height: 1200px; overflow: hidden;
    background: var(--page-bg);
    font-family: "Questrial", "Century Gothic", sans-serif;
    color: var(--ink);
  }
  .canvas {
    width: 1200px; height: 1200px;
    display: flex; flex-direction: column; align-items: center; justify-content: center;
    gap: 44px;
  }
  .card {
    position: relative;
    width: 910px; height: 520px;
    background: var(--card-bg);
    border-radius: 30px;
    overflow: hidden;
    box-shadow: 0 10px 30px rgba(0,0,0,0.12);
  }

  /* Product side */
  .product-side {
    display: flex; flex-direction: column; align-items: center; justify-content: center;
    text-align: center;
  }
  .brand-lockup { display: flex; align-items: center; gap: 18px; }
  .brand-dot {
    width: 64px; height: 64px; border-radius: 50%;
    background: linear-gradient(160deg, var(--cool-1), var(--cool-2));
  }
  .product-name {
    font-family: "Montserrat", sans-serif;
    font-weight: 600; font-size: 78px; letter-spacing: 0.5px;
    color: var(--ink-soft);
  }
  .product-tagline {
    margin-top: 14px;
    font-size: 25px; letter-spacing: 0.6px;
    color: var(--ink-soft);
  }
  .product-url {
    margin-top: 52px;
    font-family: "Montserrat", sans-serif;
    font-weight: 700; font-size: 22px; letter-spacing: 0.8px;
    color: var(--violet);
  }

  /* Contact side */
  .contact-side .org-block {
    position: absolute; left: 70px; top: 58px;
  }
  .org-lockup { display: flex; align-items: center; gap: 16px; }
  .org-dot {
    width: 44px; height: 44px; border-radius: 50%;
    background: linear-gradient(160deg, var(--warm-1), var(--warm-2) 50%, var(--warm-3));
  }
  .org-name, .org-sub {
    font-family: "Montserrat", sans-serif;
    font-weight: 600; color: var(--ink);
    text-transform: uppercase;
  }
  .org-name { font-size: 40px; letter-spacing: 9px; }
  .org-sub { margin-top: 6px; margin-left: 60px; font-size: 20px; letter-spacing: 14px; }

  .person { position: absolute; left: 70px; top: 252px; }
  .person-name {
    font-family: "Montserrat", sans-serif;
    font-weight: 700; font-size: 34px; letter-spacing: 0.5px;
    text-transform: uppercase; color: var(--ink);
  }
  .person-title { margin-top: 2px; font-size: 21px; color: var(--ink-soft); }
  .person-rule { width: 42px; height: 2px; margin-top: 12px; background: var(--accent-red); }
  .contact-list { list-style: none; margin-top: 16px; }
  .contact-list li {
    display: flex; align-items: center; gap: 12px;
    font-size: 21px; letter-spacing: 0.4px; color: var(--ink); line-height: 36px;
  }
  .contact-list svg { width: 20px; height: 20px; flex: none; }

  .decor-orb {
    position: absolute; right: -120px; bottom: -170px;
    width: 560px; height: 560px; border-radius: 50%;
    background: linear-gradient(200deg, var(--warm-1) 5%, var(--warm-2) 45%, var(--warm-3) 95%);
  }
</style>
</head>
<body>
<main class="canvas">

  <section class="card product-side" aria-label="Product side">
    <div class="brand-lockup">
      <span class="brand-dot" aria-hidden="true"></span>
      <span class="product-name">Glimworld</span>
    </div>
    <p class="product-tagline">Culturally Immersive Language Learning Games</p>
    <p class="product-url">www.glimworld-play.com</p>
  </section>

  <section class="card contact-side" aria-label="Contact side">
    <div class="org-block">
      <div class="org-lockup">
        <span class="org-dot" aria-hidden="true"></span>
        <span class="org-name">Brightloom</span>
      </div>
      <div class="org-sub">Language</div>
    </div>

    <div class="person">
      <h1 class="person-name">Perry Dunmore</h1>
      <p class="person-title">President</p>
      <div class="person-rule"></div>
      <ul class="contact-list">
        <li>
          <svg viewBox="0 0 20 20" aria-hidden="true">
            <rect x="2" y="5" width="16" height="11" rx="1.5" fill="none" stroke="#ef2b3a" stroke-width="2"/>
            <path d="M2.5 6 L10 11.5 L17.5 6" fill="none" stroke="#ef2b3a" stroke-width="2"/>
          </svg>
          pdunmore@quillpost-mail.net
        </li>
        <li>
          <svg viewBox="0 0 20 20" aria-hidden="true">
            <path d="M5 2.5 L8 2.5 L9 6.5 L7 8 C8 10.5 9.5 12 12 13 L13.5 11 L17.5 12 L17.5 15 C17.5 16.5 16 17.5 14.5 17.5 C8 17 3 12 2.5 5.5 C2.5 4 3.5 2.5 5 2.5 Z" fill="#ef2b3a"/>
          </svg>
          (555)-014-2286
        </li>
      </ul>
    </div>

    <div class="decor-orb" role="img" aria-label="Large warm gradient brand decoration"></div>
  </section>

</main>
</body>
</html>
```